Summit Ridge Business Card

Side 1: Summit Ridge Logo (logo without Maltese cross) with industrial rope rescue related theme. Our company services - TRAINING - Fire Training, Confined Space Rescue Training, Rope Rescue training, Hazmat Training, Incident Command, EMS, Pump Operations Training. Website - summitridgeexample.com.
Side 2: Summit Ridge Fire Department Logo (logo with Maltese cross) with Firefighter related theme. Company (division) services - FIELD SERVICES - Fire Department, Stand-by Rescue, Safety, EMS, Planning. "Supporting the Emergency Response Community Since 1967"

Add contact information wherever it makes since (Name, Email, Phone).
I would like it to represent the Summit Ridge Fire Department Logo as a division not as a separate entity without saying it, possibly by depicting it in the background of Side 2 instead of being a standalone picture like the logo on Side 1.

```html
<!DOCTYPE html>
<html lang="en">
<head>
<meta charset="utf-8">
<title>Summit Ridge Business Card</title>
<link href="https://fonts.googleapis.com/css2?family=Montserrat:wght@400;500;600;800&display=swap" rel="stylesheet">
<style>
  :root{
    --page:#d4d4d4;
    --card:#ffffff;
    --card-back:#f1f1f1;
    --red:#e0262d;
    --ink:#4a4a4c;
    --rule:#3d3d3f;
  }
  *{box-sizing:border-box;margin:0;padding:0}
  html,body{width:1200px;height:1200px;overflow:hidden}
  body{
    background:var(--page);
    font-family:"Montserrat",Arial,sans-serif;
    color:var(--ink);
    display:flex;flex-direction:column;align-items:center;justify-content:center;gap:70px;
  }
  .card{
    width:820px;height:468px;border-radius:26px;
    box-shadow:0 10px 26px rgba(0,0,0,.18);
    position:relative;
  }
  .card--front{background:var(--card);display:flex;flex-direction:column;align-items:center;justify-content:center;text-align:center}
  .card--back{background:var(--card-back)}

  .brand{display:flex;align-items:center;gap:14px}
  .brand__mark{width:22px;height:22px;background:var(--red)}
  .brand__name{font-weight:800;color:var(--red);letter-spacing:.02em;text-transform:uppercase}
  .card--front .brand__name{font-size:44px}
  .card--front .brand{margin-bottom:44px}

  .services{font-size:19px;line-height:1.5}
  .services__label{color:var(--red);font-weight:600;text-transform:uppercase}
  .tagline{margin-top:22px;color:var(--red);font-size:19px;font-weight:500}

  .back__brand{position:absolute;left:56px;top:150px;width:340px;justify-content:center}
  .card--back .brand__name{font-size:38px}
  .divider{position:absolute;left:420px;top:60px;width:2px;height:250px;background:var(--rule)}
  .contact{position:absolute;left:456px;top:56px}
  .contact__name{font-size:34px;font-weight:800;color:var(--red)}
  .contact__role{font-size:18px;margin:4px 0 14px}
  .contact__addr{font-size:18px;line-height:1.4;margin-bottom:12px}
  .contact__list{list-style:none;font-size:17px;line-height:1.65}
  .contact__list li{display:flex;align-items:center;gap:12px}
  .contact__list svg{width:18px;height:18px;flex:none}
  .back__services{position:absolute;left:0;right:0;bottom:44px;text-align:center;font-size:18px;line-height:1.5}
</style>
</head>
<body>

<section class="card card--front" aria-label="Card side with field services">
  <div class="brand">
    <span class="brand__mark"></span>
    <span class="brand__name">Summit Ridge</span>
  </div>
  <p class="services"><span class="services__label">Field Services</span> - Fire Department | Stand-by Rescue |<br>Safety | EMS | Planning</p>
  <p class="tagline">Supporting the Emergency Response Community Since 1967</p>
</section>

<section class="card card--back" aria-label="Card side with contact details">
  <div class="brand back__brand">
    <span class="brand__mark"></span>
    <span class="brand__name">Summit Ridge</span>
  </div>
  <div class="divider"></div>
  <div class="contact">
    <p class="contact__name">Dana Whitfield</p>
    <p class="contact__role">Founder &amp; Director</p>
    <p class="contact__addr">418 Harbor Lane<br>Port Alder, TX 77000</p>
    <ul class="contact__list">
      <li><svg viewBox="0 0 24 24" fill="#e0262d"><path d="M6.6 10.8a15 15 0 0 0 6.6 6.6l2.2-2.2c.3-.3.7-.4 1-.2 1.1.4 2.3.6 3.6.6.6 0 1 .4 1 1V20c0 .6-.4 1-1 1A17 17 0 0 1 3 4c0-.6.4-1 1-1h3.5c.6 0 1 .4 1 1 0 1.3.2 2.5.6 3.6.1.3 0 .7-.2 1z"/></svg>(555) 014-0627</li>
      <li><svg viewBox="0 0 24 24" fill="#e0262d"><path d="M2 5h20v14H2z"/><path d="M2 5l10 8 10-8" fill="none" stroke="#fff" stroke-width="2"/></svg>whitfield@summitridgeexample.com</li>
      <li><svg viewBox="0 0 24 24" fill="none" stroke="#e0262d" stroke-width="2"><circle cx="12" cy="12" r="9"/><path d="M3 12h18M12 3c3 3 3 15 0 18M12 3c-3 3-3 15 0 18"/></svg>www.summitridgeexample.com</li>
    </ul>
  </div>
  <p class="back__services"><span class="services__label">Training</span> - Fire Training | Confined Space Rescue Training |<br>Hazmat Training | Incident Command | EMS | Pump Operations Training</p>
</section>

</body>
</html>
```